Business Card for Field Lotus-Eco Friendly Organic Clothing Brand

We are looking for an amazing business card for our eco friendly, organic clothing brand. We are thinking maybe a business card with a peel off sticker on the back, since our hanging clothing tag is a peel off sticker on the back. I will attach our hang tag so we can make sure we stay in line with our design. I've also attached a bag we are doing because I do like the scattered emblem look as well.

```html
<!DOCTYPE html>
<html lang="en">
<head>
<meta charset="UTF-8">
<title>Field Lotus – Business Card</title>
<link href="https://fonts.googleapis.com/css2?family=Source+Sans+3:wght@400;600;700&display=swap" rel="stylesheet">
<style>
  :root {
    --page-bg: #efece6;
    --gold-light: #ecd48c;
    --gold-mid: #dcb657;
    --gold-deep: #cf9f3a;
    --ink: #1d1a14;
    --ink-soft: #2c261a;
    --emboss-light: rgba(255, 240, 190, 0.55);
    --emboss-dark: rgba(120, 80, 10, 0.35);
  }
  * { box-sizing: border-box; margin: 0; padding: 0; }
  html, body {
    width: 1200px;
    height: 900px;
    overflow: hidden;
    background: var(--page-bg);
    font-family: "Source Sans 3", "Myriad Pro", sans-serif;
    color: var(--ink);
  }
  .canvas { position: relative; width: 1200px; height: 900px; }

  .card {
    position: absolute;
    height: 342px;
    box-shadow: 0 6px 18px rgba(0, 0, 0, 0.18);
  }
  .card-front {
    left: 238px; top: 62px; width: 555px;
    background: linear-gradient(180deg, var(--gold-light) 0%, var(--gold-mid) 60%, var(--gold-deep) 100%);
  }
  .card-back {
    left: 457px; top: 518px; width: 560px;
    background: radial-gradient(ellipse 55% 60% at 52% 45%, #f0dc9c 0%, var(--gold-mid) 55%, var(--gold-deep) 100%);
  }

  .brand-mark {
    position: absolute;
    left: 268px; top: 92px;
    display: flex; align-items: center; gap: 12px;
  }
  .brand-mark .square {
    width: 26px; height: 26px;
    background: var(--ink);
  }
  .brand-mark .name {
    font-size: 34px; font-weight: 700;
    color: var(--ink); letter-spacing: 0.5px;
  }

  .holder { position: absolute; left: 43px; top: 180px; }
  .holder .person { font-size: 20px; font-weight: 700; color: var(--ink); }
  .holder .role { font-size: 15px; color: var(--ink-soft); margin-top: 1px; }

  .contacts {
    position: absolute; left: 43px; top: 244px;
    list-style: none; font-size: 15px; color: var(--ink-soft);
  }
  .contacts li { display: flex; align-items: center; gap: 10px; height: 20px; }
  .contacts svg { width: 11px; height: 11px; fill: var(--ink); flex: none; }

  .address {
    position: absolute; right: 43px; top: 264px;
    text-align: right; font-size: 15px; line-height: 20px; color: var(--ink-soft);
  }

  .back-emblem {
    position: absolute; left: 190px; top: 42px;
    width: 180px; height: 180px; border-radius: 50%;
    background: radial-gradient(circle, #f3e2a8 0%, #e2c06a 100%);
    box-shadow: inset 2px 2px 3px var(--emboss-light), inset -2px -2px 3px var(--emboss-dark);
  }
  .back-name {
    position: absolute; left: 0; right: 0; top: 272px;
    text-align: center; font-size: 38px; font-weight: 600;
    color: #f4e3a6; letter-spacing: 1px;
  }
</style>
</head>
<body>
<main class="canvas">
  <section class="card card-front" aria-label="Business card front">
    <div class="brand-mark">
      <span class="square"></span>
      <span class="name">Field Lotus</span>
    </div>

    <div class="holder">
      <p class="person">Daniel Carter</p>
      <p class="role">Managing Director</p>
    </div>

    <ul class="contacts">
      <li>
        <svg viewBox="0 0 24 24" aria-hidden="true"><path d="M6.6 10.8a15.1 15.1 0 0 0 6.6 6.6l2.2-2.2a1 1 0 0 1 1-.25 11.4 11.4 0 0 0 3.6.57 1 1 0 0 1 1 1V20a1 1 0 0 1-1 1A17 17 0 0 1 3 4a1 1 0 0 1 1-1h3.5a1 1 0 0 1 1 1c0 1.25.2 2.45.57 3.6a1 1 0 0 1-.25 1z"/></svg>
        <span>012-345 678 910</span>
      </li>
      <li>
        <svg viewBox="0 0 24 24" aria-hidden="true"><path d="M2 5h20v14H2z M2 5l10 8 10-8" /></svg>
        <span>hello@fieldlotus.com</span>
      </li>
      <li>
        <svg viewBox="0 0 24 24" aria-hidden="true"><circle cx="12" cy="12" r="11"/></svg>
        <span>www.fieldlotus.com</span>
      </li>
    </ul>

    <address class="address">
      12345, Address Goes Here<br>
      Country Name, 123456.
    </address>
  </section>

  <section class="card card-back" aria-label="Business card back">
    <div class="back-emblem" role="img" aria-label="Embossed brand emblem area"></div>
    <p class="back-name">Field Lotus</p>
  </section>
</main>
</body>
</html>
```